Woman owned consulting company needs an elegant and modern business card design

I need a business card design for my new consulting company, Mara Quillon Consulting. I am looking for something that is simple and elegant, but also creative and original. You can use either version of the logo that are attached. I have also included the information that needs to be featured on the business card.

Contact Information for Business Card

Requirements
Must have
• The logo and the font type and a standard business card size. Use shades of gray/silver and or rose gold that are in the logo.
• I didn't realize that my actual logo wasn't attached. Please incorporate in the designs.
Should not have
• Colors that are different from my logo

```html
<!DOCTYPE html>
<html lang="en">
<head>
<meta charset="utf-8">
<title>Mara Quillon Consulting – Business Card</title>
<link href="https://fonts.googleapis.com/css2?family=Inter:wght@300;400&display=swap" rel="stylesheet">
<style>
  :root {
    --backdrop: #e3e3e3;
    --card: #fdfdfd;
    --rose: #c0688f;
    --silver: #7e8085;
  }
  * { box-sizing: border-box; margin: 0; padding: 0; }
  html, body {
    width: 1200px;
    height: 991px;
    overflow: hidden;
    background: var(--backdrop);
    font-family: "Inter", "Helvetica Neue", Arial, sans-serif;
    font-weight: 300;
  }
  .canvas { position: relative; width: 1200px; height: 991px; }
  .card {
    position: absolute;
    left: 304px;
    width: 592px;
    height: 329px;
    background: var(--card);
    border-radius: 19px;
    overflow: hidden;
  }
  .card--front { top: 145px; }
  .card--back { top: 517px; }

  .title-line {
    position: absolute;
    left: 44px;
    top: 56px;
    font-size: 17px;
    letter-spacing: 0.2px;
    color: var(--silver);
  }
  .title-line .person { color: var(--rose); font-weight: 400; }
  .title-line .divider { margin: 0 10px; }

  .contact {
    position: absolute;
    left: 44px;
    top: 240px;
    font-size: 13.3px;
    line-height: 24px;
    color: var(--silver);
    letter-spacing: 0.1px;
  }
  .contact .divider { color: var(--rose); margin: 0 7px; }
  .contact .web { color: var(--rose); }

  .front-name {
    position: absolute;
    right: 44px;
    top: 250px;
    font-size: 15px;
    line-height: 18px;
    text-align: right;
    color: var(--silver);
    letter-spacing: 1px;
  }

  .back-name {
    position: absolute;
    left: 0;
    right: 0;
    top: 80px;
    text-align: center;
    font-size: 74px;
    line-height: 1;
    letter-spacing: -1px;
    color: var(--rose);
  }
  .company {
    position: absolute;
    left: 0;
    right: 0;
    top: 258px;
    text-align: center;
    font-size: 24px;
    color: var(--silver);
    letter-spacing: 0.2px;
  }
</style>
</head>
<body>
<div class="canvas">
  <section class="card card--front">
    <p class="title-line"><span class="person">MARA QUILLON</span><span class="divider">|</span>OWNER</p>
    <div class="contact">
      <p>555-014-2290<span class="divider">|</span>MARA@MARAQUILLONCONSULTING.COM</p>
      <p class="web">WWW.MARAQUILLONCONSULTING.COM</p>
    </div>
    <p class="front-name">MARA<br>QUILLON</p>
  </section>

  <section class="card card--back">
    <p class="back-name">MARA QUILLON</p>
    <p class="company">MARA QUILLON CONSULTING, LLC</p>
  </section>
</div>
</body>
</html>
```